body balm label design

body balm tube design, current label design for other similar products
Need to have a design which can interchange between 3 different solutions
Amber Tide (Lavender + Vanilla)
Copper Ridge (Eucalyptus + Mint)
Fern Hollow (Bergamot + Cedarwood)
Tube size:
2.5h x 3.25 w
Target Market(s)
natural, solution focused
Requirements
Must have
- relatable to existing brand designs, focus on features and benefits

```html
<!DOCTYPE html>
<html lang="en">
<head>
<meta charset="utf-8">
<title>Verdant Oak Natural Body Balm Labels</title>
<link rel="stylesheet" href="https://fonts.googleapis.com/css2?family=Cormorant+Garamond:wght@500&family=Montserrat:wght@300;400;600&family=Mrs+Saint+Delafield&display=swap">
<style>
  :root {
    --paper: #ffffff;
    --stage: #eef0f3;
    --slate: #889ca8;
    --slate-deep: #7b8f9b;
    --slate-faint: #d6dee3;
    --sage: #aebf9e;
    --sage-deep: #a3b592;
    --sage-faint: #dde5d6;
    --fern: #6a9657;
    --fern-deep: #5f8a4d;
    --fern-faint: #d4e2cc;
    --ink-soft: #8d9aa3;
    --ink-head: #6f7f89;
    --serif: "Cormorant Garamond", Georgia, serif;
    --sans: "Montserrat", Arial, sans-serif;
    --script: "Mrs Saint Delafield", cursive;
  }
  * { box-sizing: border-box; margin: 0; padding: 0; }
  html, body { width: 960px; height: 1200px; overflow: hidden; background: var(--paper); }
  .canvas { position: relative; width: 960px; height: 1200px; }

  /* ---------- front label row ---------- */
  .range { position: absolute; left: 0; top: 0; width: 960px; height: 629px; background: var(--paper); }
  .front {
    position: absolute; top: 192px; width: 132px; height: 400px;
    background: var(--paper); border: 1px solid #e6e9ec; overflow: hidden;
  }
  .front--amber { left: 114px; --tone: var(--slate); --tone-deep: var(--slate-deep); --faint: var(--slate-faint); }
  .front--fern { left: 408px; --tone: var(--sage); --tone-deep: var(--sage-deep); --faint: var(--sage-faint); }
  .front--copper { left: 716px; --tone: var(--fern); --tone-deep: var(--fern-deep); --faint: var(--fern-faint); }

  .front__botanical {
    position: absolute; left: 0; top: 40px; width: 92px; height: 330px;
    background: radial-gradient(ellipse at 40% 45%, var(--faint) 0%, rgba(255,255,255,0) 70%);
    opacity: .8;
  }
  .front__word {
    position: absolute; left: 4px; top: 76px; height: 150px;
    writing-mode: vertical-rl; transform: rotate(180deg);
    font: 500 36px/1 var(--serif); letter-spacing: 3px; color: var(--tone-deep);
  }
  .front__script {
    position: absolute; left: 38px; top: 96px; height: 70px;
    writing-mode: vertical-rl; transform: rotate(180deg);
    font: 24px/1 var(--script); color: var(--tone-deep);
  }
  .front__rule { position: absolute; left: 48px; top: 168px; width: 1.5px; height: 222px; background: var(--tone); }

  .arch {
    position: absolute; background: var(--tone); color: #fff; text-align: center;
  }
  .front .arch { left: 64px; top: 76px; width: 68px; height: 314px; border-radius: 34px 34px 0 0; }
  .arch__brand { position: absolute; left: 0; top: 0; width: 100%; }
  .arch__brand text { fill: #fff; font-family: var(--serif); letter-spacing: 1px; }
  .arch__sprig { position: absolute; left: 50%; transform: translateX(-50%); border-radius: 40% 40% 50% 50%; background: rgba(255,255,255,.28); }
  .front .arch__sprig { top: 20px; width: 36px; height: 56px; }
  .arch__title { position: absolute; left: 0; width: 100%; font-family: var(--sans); font-weight: 300; line-height: 1.22; letter-spacing: .5px; }
  .front .arch__title { top: 110px; font-size: 11px; }
  .arch__seal { position: absolute; left: 50%; transform: translateX(-50%); }
  .arch__seal text { fill: #fff; }
  .front .arch__seal { top: 222px; width: 44px; height: 44px; }
  .arch__weight { position: absolute; left: 0; width: 100%; font-family: var(--sans); font-weight: 300; line-height: 1.3; }
  .front .arch__weight { top: 272px; font-size: 7px; }

  /* ---------- full wrap label ---------- */
  .stage { position: absolute; left: 0; top: 629px; width: 960px; height: 571px; background: var(--stage); }
  .wrap {
    position: absolute; left: 172px; top: 685px; width: 616px; height: 452px;
    background: var(--paper); overflow: hidden;
    --tone: var(--slate); --tone-deep: var(--slate-deep);
  }
  .wrap__botanical {
    position: absolute; left: 24px; top: 15px; width: 360px; height: 420px;
    background: radial-gradient(ellipse at 45% 45%, #e3e9ec 0%, #eef2f4 45%, rgba(255,255,255,0) 72%);
  }
  .wrap__word {
    position: absolute; left: 188px; top: 71px; height: 188px;
    writing-mode: vertical-rl; transform: rotate(180deg);
    font: 500 54px/1 var(--serif); letter-spacing: 4px; color: var(--slate-deep);
  }
  .wrap__script {
    position: absolute; left: 236px; top: 108px; height: 80px;
    writing-mode: vertical-rl; transform: rotate(180deg);
    font: 30px/1 var(--script); color: var(--slate-deep);
  }
  .wrap__rule { position: absolute; left: 248px; top: 175px; width: 2px; height: 277px; background: var(--slate); }
  .wrap .arch { left: 268px; top: 77px; width: 87px; height: 375px; border-radius: 43.5px 43.5px 0 0; }
  .wrap .arch__sprig { top: 30px; width: 54px; height: 70px; }
  .wrap .arch__title { top: 130px; font-size: 14.5px; }
  .wrap .arch__seal { top: 258px; width: 52px; height: 52px; }
  .wrap .arch__weight { top: 326px; font-size: 9px; }

  .wrap__scent {
    position: absolute; left: 262px; top: 240px; width: 330px; text-align: center;
    transform: rotate(-90deg); transform-origin: 50% 50%;
    left: 259px; top: 240px;
    font: 46px/1 var(--script); color: var(--slate-deep);
  }
  .wrap__info { position: absolute; left: 490px; width: 110px; font-family: var(--sans); color: var(--ink-soft); font-size: 8.6px; line-height: 1.22; letter-spacing: .9px; font-weight: 300; }
  .wrap__info h3 { font-size: 8.6px; font-weight: 600; color: var(--ink-head); letter-spacing: 1px; }
  .wrap__info--ingredients { top: 83px; }
  .wrap__info--usage { top: 203px; }
  .wrap__info--usage h3 { margin-bottom: 8px; }
  .social { position: absolute; left: 502px; top: 374px; display: flex; gap: 10px; }
  .social span { display: block; width: 19px; height: 19px; border-radius: 50%; background: var(--slate-deep); }
  .maker { position: absolute; left: 490px; top: 409px; font-family: var(--sans); font-size: 8.6px; letter-spacing: 1px; color: var(--ink-soft); font-weight: 300; line-height: 1.6; }
  .maker strong { font-weight: 600; color: var(--ink-head); }
</style>
</head>
<body>
<main class="canvas">

  <section class="range" aria-label="Front labels for the three balms">

    <article class="front front--amber">
      <div class="front__botanical" role="img" aria-label="Faint line drawing of lavender and vanilla blossoms"></div>
      <div class="front__word">AMBER</div>
      <div class="front__script">tide</div>
      <div class="front__rule"></div>
      <div class="arch">
        <svg class="arch__brand" viewBox="0 0 68 40" width="68" height="40"><path id="fa" d="M8,36 A26,26 0 0 1 60,36" fill="none"/><text font-size="6.5"><textPath href="#fa" startOffset="50%" text-anchor="middle">VERDANT OAK</textPath></text></svg>
        <div class="arch__sprig" role="img" aria-label="Small lavender and vanilla sprig drawing"></div>
        <div class="arch__title">NATURAL<br>BODY<br>BALM</div>
        <svg class="arch__seal" viewBox="0 0 44 44"><path id="sa" d="M8,30 A15,15 0 1 1 36,30" fill="none"/><text font-size="6" font-family="Cormorant Garamond, serif"><textPath href="#sa" startOffset="50%" text-anchor="middle">Made In Canada</textPath></text><text x="22" y="24" font-size="6.5" text-anchor="middle" font-family="Cormorant Garamond, serif">100%</text><text x="22" y="30" font-size="3.6" text-anchor="middle" font-family="Cormorant Garamond, serif">NATURAL</text></svg>
        <div class="arch__weight">NET WT<br>8 oz<br>/226g</div>
      </div>
    </article>

    <article class="front front--fern">
      <div class="front__botanical" role="img" aria-label="Faint line drawing of bergamot fruit and leaves"></div>
      <div class="front__word">FERN</div>
      <div class="front__script">hollow</div>
      <div class="front__rule"></div>
      <div class="arch">
        <svg class="arch__brand" viewBox="0 0 68 40" width="68" height="40"><path id="fb" d="M8,36 A26,26 0 0 1 60,36" fill="none"/><text font-size="6.5"><textPath href="#fb" startOffset="50%" text-anchor="middle">VERDANT OAK</textPath></text></svg>
        <div class="arch__sprig" role="img" aria-label="Small bergamot sprig drawing"></div>
        <div class="arch__title">NATURAL<br>BODY<br>BALM</div>
        <svg class="arch__seal" viewBox="0 0 44 44"><path id="sb" d="M8,30 A15,15 0 1 1 36,30" fill="none"/><text font-size="6" font-family="Cormorant Garamond, serif"><textPath href="#sb" startOffset="50%" text-anchor="middle">Made In Canada</textPath></text><text x="22" y="24" font-size="6.5" text-anchor="middle" font-family="Cormorant Garamond, serif">100%</text><text x="22" y="30" font-size="3.6" text-anchor="middle" font-family="Cormorant Garamond, serif">NATURAL</text></svg>
        <div class="arch__weight">NET WT<br>8 oz<br>/226g</div>
      </div>
    </article>

    <article class="front front--copper">
      <div class="front__botanical" role="img" aria-label="Faint line drawing of eucalyptus branches"></div>
      <div class="front__word">COPPER</div>
      <div class="front__script">ridge</div>
      <div class="front__rule"></div>
      <div class="arch">
        <svg class="arch__brand" viewBox="0 0 68 40" width="68" height="40"><path id="fc" d="M8,36 A26,26 0 0 1 60,36" fill="none"/><text font-size="6.5"><textPath href="#fc" startOffset="50%" text-anchor="middle">VERDANT OAK</textPath></text></svg>
        <div class="arch__sprig" role="img" aria-label="Small eucalyptus sprig drawing"></div>
        <div class="arch__title">NATURAL<br>BODY<br>BALM</div>
        <svg class="arch__seal" viewBox="0 0 44 44"><path id="sc" d="M8,30 A15,15 0 1 1 36,30" fill="none"/><text font-size="6" font-family="Cormorant Garamond, serif"><textPath href="#sc" startOffset="50%" text-anchor="middle">Made In Canada</textPath></text><text x="22" y="24" font-size="6.5" text-anchor="middle" font-family="Cormorant Garamond, serif">100%</text><text x="22" y="30" font-size="3.6" text-anchor="middle" font-family="Cormorant Garamond, serif">NATURAL</text></svg>
        <div class="arch__weight">NET WT<br>8 oz<br>/226g</div>
      </div>
    </article>

  </section>

  <section class="stage" aria-hidden="true"></section>

  <article class="wrap" aria-label="Amber Tide full wrap label">
    <div class="wrap__botanical" role="img" aria-label="Large faint line drawing of vanilla orchid blossoms and leaves"></div>
    <div class="wrap__word">AMBER</div>
    <div class="wrap__script">tide</div>
    <div class="wrap__rule"></div>
    <div class="arch">
      <svg class="arch__brand" viewBox="0 0 87 50" width="87" height="50"><path id="wa" d="M10,46 A33.5,33.5 0 0 1 77,46" fill="none"/><text font-size="8.5"><textPath href="#wa" startOffset="50%" text-anchor="middle">VERDANT OAK</textPath></text></svg>
      <div class="arch__sprig" role="img" aria-label="Small lavender and vanilla sprig drawing"></div>
      <div class="arch__title">NATURAL<br>BODY<br>BALM</div>
      <svg class="arch__seal" viewBox="0 0 44 44"><path id="sw" d="M8,30 A15,15 0 1 1 36,30" fill="none"/><text font-size="6" font-family="Cormorant Garamond, serif"><textPath href="#sw" startOffset="50%" text-anchor="middle">Made In Canada</textPath></text><text x="22" y="24" font-size="6.5" text-anchor="middle" font-family="Cormorant Garamond, serif">100%</text><text x="22" y="30" font-size="3.6" text-anchor="middle" font-family="Cormorant Garamond, serif">NATURAL</text></svg>
      <div class="arch__weight">NET WT<br>8 oz<br>/226g</div>
    </div>

    <div class="wrap__scent">Lavender + Vanilla</div>

    <div class="wrap__info wrap__info--ingredients">
      <h3>Ingredients:</h3>
      <p>Shea butter, cocoa butter, coconut oil, sweet almond oil, beeswax, lavender essential oil, vanilla extract or vanilla oleoresin, vitamin E oil</p>
    </div>
    <div class="wrap__info wrap__info--usage">
      <h3>How to use:</h3>
      <p>Scoop a small amount, warm it between your palms, apply to dry skin areas, gently massage in, let it absorb, use as needed.</p>
    </div>

    <div class="social" aria-label="Social channels"><span></span><span></span><span></span></div>
    <div class="maker">Made by Verdant Oak<br><strong>WWW.VERDANTOAK.CA</strong></div>
  </article>

</main>
</body>
</html>
```